Looking for a cool & simple business-card-design for digital agency

Hi!

We are a web agency that offers Reputation Management, Vextor & Seo Services and software development. We like cool things, we like innovative styles.

We have uploaded our logo.

Project Deadline Extended Reason: Client does not want any designs with the colorful logo. Please send us submissions ONLY with the blac and white logo. What the client would like to see:1) Back of the card: is a silver logo on a black background2) front of the card with all the data, please use white background and black logo thank you Added Friday, May 8, 2015

Industry/Entity Type

Software

```html
<!DOCTYPE html>
<html lang="de">
<head>
<meta charset="utf-8">
<title>Nordwerk AG – Visitenkarte</title>
<link rel="stylesheet" href="https://fonts.googleapis.com/css2?family=Lato:wght@400;700;900&display=swap">
<style>
  :root {
    --backdrop: #3a322b;
    --card-black: #050505;
    --card-white: #ffffff;
    --ink: #141414;
    --silver: #a3a3a3;
    --silver-faint: #161616;
    --white-text: #ffffff;
  }
  * { box-sizing: border-box; margin: 0; padding: 0; }
  html, body {
    width: 1200px; height: 905px; overflow: hidden;
    background: var(--backdrop);
    font-family: "Lato", Arial, sans-serif;
  }
  .stage { position: relative; width: 1200px; height: 905px; }

  .card {
    position: absolute;
    width: 600px; height: 343px;
    overflow: hidden;
    box-shadow: 0 10px 28px rgba(0,0,0,.45);
  }

  /* Back side */
  .card-back { left: 70px; top: 60px; background: var(--card-black); }
  .card-back .decor-block {
    position: absolute; left: 150px; top: 30px;
    width: 300px; height: 300px;
    background: var(--silver-faint);
    border-radius: 18px;
  }
  .brand {
    position: absolute; display: flex; align-items: center; gap: 10px;
    font-weight: 900; letter-spacing: .5px; white-space: nowrap;
  }
  .brand-mark { width: 22px; height: 22px; flex: none; }
  .card-back .brand { left: 48px; top: 86px; font-size: 40px; color: var(--silver); }
  .card-back .brand-mark { background: var(--silver); }
  .services {
    position: absolute; left: 200px; top: 170px;
    list-style: none;
    color: var(--white-text); font-weight: 700; font-size: 22px; line-height: 1.2;
    text-align: center;
  }

  /* Front side */
  .card-front { left: 530px; top: 480px; background: var(--card-white); }
  .card-front .decor-block {
    position: absolute; right: -40px; top: -40px;
    width: 260px; height: 260px;
    background: var(--ink);
    border-radius: 22px;
  }
  .card-front .brand { left: 40px; top: 78px; font-size: 30px; color: var(--ink); }
  .card-front .brand-mark { background: var(--ink); width: 18px; height: 18px; }
  .person { position: absolute; left: 40px; top: 170px; color: var(--ink); }
  .person-name { font-weight: 900; font-size: 22px; }
  .person-role { font-size: 17px; margin-top: 2px; }
  .contacts {
    position: absolute; left: 40px; top: 238px;
    list-style: none; color: var(--ink); font-size: 18px; line-height: 23px;
  }
  .contacts li { display: flex; align-items: center; gap: 8px; white-space: nowrap; }
  .contacts svg { width: 15px; height: 15px; fill: var(--ink); flex: none; }
  .contacts .icon-line { fill: none; stroke: var(--ink); stroke-width: 1.4; }
</style>
</head>
<body>
<main class="stage">

  <section class="card card-back" aria-label="Kartenrückseite">
    <div class="decor-block"></div>
    <div class="brand"><span class="brand-mark"></span>Nordwerk AG</div>
    <ul class="services">
      <li>Reputation Management</li>
      <li>Vextor &amp; Seo Services</li>
      <li>Software development.</li>
    </ul>
  </section>

  <section class="card card-front" aria-label="Kartenvorderseite">
    <div class="decor-block"></div>
    <div class="brand"><span class="brand-mark"></span>Nordwerk AG</div>
    <div class="person">
      <p class="person-name">Lena Hartmann</p>
      <p class="person-role">Director</p>
    </div>
    <ul class="contacts">
      <li>
        <svg viewBox="0 0 16 16" aria-hidden="true"><path d="M2 5c0-2 2-3 6-3s6 1 6 3v1h-3V5H5v1H2z M4 7h8l2 7H2z"/></svg>
        040 218 5573
      </li>
      <li>
        <svg viewBox="0 0 16 16" aria-hidden="true"><path d="M4 1h8v14H4z M5.5 3v9h5V3z"/></svg>
        171 3926 480
      </li>
      <li>
        <svg viewBox="0 0 16 16" aria-hidden="true"><path d="M1 3h14v10H1z M2 4.5v.5l6 4 6-4v-.5z"/></svg>
        info@nordwerkag.com
      </li>
      <li>
        <svg viewBox="0 0 16 16" aria-hidden="true">
          <g class="icon-line">
            <circle cx="8" cy="8" r="6.5"/>
            <ellipse cx="8" cy="8" rx="2.8" ry="6.5"/>
            <line x1="1.5" y1="8" x2="14.5" y2="8"/>
            <line x1="2.6" y1="4.8" x2="13.4" y2="4.8"/>
            <line x1="2.6" y1="11.2" x2="13.4" y2="11.2"/>
          </g>
        </svg>
        www.nordwerkag.com
      </li>
    </ul>
  </section>

</main>
</body>
</html>
```